Colin Vardek Business card

Hey there, I’m hoping to have a business card designed. I’m in Real estate and just switched to a new Brokerage called: The Harbourline Property Group

The back could just be the company name maybe or whatever looks good!

I’ve attached some logos of our company and some cards my buddy had done up.

On the card:
Colin Vardek
colinvardek@mailora.com
587-412-9065
colinvardek.ca

Target Market(s)

Home buyers and sellers

Industry/Entity Type

Real Estate

Contact Information for Business Card

just looking for a cool and modern design with my picture on it. I like the idea of Black and red being used.

Requirements
Must have
• all the details provided. I'm open to anything. Just want a professional looking card.

```html
<!DOCTYPE html>
<html lang="en">
<head>
<meta charset="UTF-8">
<title>Colin Vardek – Business Card</title>
<link href="https://fonts.googleapis.com/css2?family=Poppins:wght@400;500;600&display=swap" rel="stylesheet">
<style>
  :root {
    --stage: #2b2b2d;
    --card-dark: #1d1e20;
    --brand-red: #d11a36;
    --photo-wall: #e4e4e6;
    --photo-shade: #c6c6c9;
    --photo-suit: #2a2c31;
    --text-light: #ffffff;
    --pattern-text: #2b2c30;
  }
  * { box-sizing: border-box; margin: 0; padding: 0; }
  html, body { width: 1200px; height: 1108px; overflow: hidden; }
  body {
    background: var(--stage);
    font-family: "Poppins", sans-serif;
    display: flex;
    align-items: center;
    justify-content: center;
    gap: 80px;
  }
  .card {
    position: relative;
    width: 440px;
    height: 690px;
    border-radius: 22px;
    overflow: hidden;
    background: var(--card-dark);
    box-shadow: 0 18px 40px rgba(0,0,0,0.45);
  }

  /* Front */
  .card-front__photo {
    position: absolute;
    inset: 0 0 auto 0;
    height: 500px;
    background:
      radial-gradient(ellipse 150px 210px at 62% 78%, var(--photo-suit) 0%, rgba(42,44,49,0.85) 45%, rgba(42,44,49,0) 100%),
      repeating-linear-gradient(90deg, rgba(0,0,0,0) 0 108px, rgba(0,0,0,0.05) 108px 110px),
      linear-gradient(160deg, var(--photo-wall) 0%, var(--photo-shade) 100%);
  }
  .card-front__shapes { position: absolute; inset: 0; }
  .card-front__info {
    position: absolute;
    left: 0; right: 0;
    top: 468px;
    text-align: center;
    color: var(--text-light);
  }
  .agent-name {
    font-weight: 500;
    font-size: 32px;
    letter-spacing: 0.5px;
    color: var(--brand-red);
    text-transform: uppercase;
    line-height: 1;
  }
  .contact-icons {
    margin: 22px auto 12px;
    display: flex;
    align-items: center;
    justify-content: center;
    gap: 8px;
  }
  .contact-icons__rule { width: 38px; height: 1.5px; background: var(--brand-red); }
  .contact-icons svg { display: block; }
  .contact-list { list-style: none; }
  .contact-list li { font-size: 21px; line-height: 1.32; font-weight: 400; }

  /* Back */
  .card-back__pattern {
    position: absolute;
    inset: 0;
    background: linear-gradient(135deg, rgba(255,255,255,0.05) 0%, rgba(255,255,255,0) 45%, rgba(255,255,255,0.04) 100%);
  }
  .pattern-row {
    position: absolute;
    left: -120px;
    white-space: nowrap;
    font-weight: 600;
    font-size: 24px;
    letter-spacing: 0.5px;
    color: var(--pattern-text);
    text-transform: uppercase;
  }
  .pattern-row:nth-child(even) { left: -300px; }
  .card-back__brand {
    position: absolute;
    inset: 0;
    display: flex;
    align-items: center;
    justify-content: center;
    gap: 14px;
    padding: 0 40px;
  }
  .brand-mark { width: 18px; height: 18px; background: var(--brand-red); flex: none; }
  .brand-name {
    font-weight: 600;
    font-size: 26px;
    line-height: 1.2;
    color: var(--text-light);
    text-transform: uppercase;
  }
</style>
</head>
<body>
  <section class="card card-front">
    <div class="card-front__photo" role="img" aria-label="Portrait photo of Colin Vardek in a dark blazer and white shirt against a light panelled wall"></div>
    <svg class="card-front__shapes" width="440" height="690" viewBox="0 0 440 690" aria-hidden="true">
      <polygon points="0,300 440,470 440,690 0,690" fill="var(--brand-red)"/>
      <polygon points="0,345 440,500 440,690 0,690" fill="var(--card-dark)"/>
    </svg>
    <div class="card-front__info">
      <h1 class="agent-name">Colin Vardek</h1>
      <div class="contact-icons" aria-hidden="true">
        <span class="contact-icons__rule"></span>
        <svg width="30" height="30" viewBox="0 0 30 30"><circle cx="15" cy="15" r="15" fill="var(--brand-red)"/><path d="M11 9l3 0 1 4-2 1.5a8 8 0 0 0 3.5 3.5L18 16l4 1v3c0 1-1 1.5-2 1.5A12 12 0 0 1 8.5 10c0-1 .5-1 2.5-1z" fill="#fff"/></svg>
        <svg width="30" height="30" viewBox="0 0 30 30"><circle cx="15" cy="15" r="15" fill="var(--brand-red)"/><rect x="8" y="10" width="14" height="10" fill="#fff"/><path d="M8 10l7 6 7-6" fill="none" stroke="var(--brand-red)" stroke-width="1.3"/></svg>
        <svg width="30" height="30" viewBox="0 0 30 30"><circle cx="15" cy="15" r="15" fill="var(--brand-red)"/><g fill="none" stroke="#fff" stroke-width="1.3"><circle cx="15" cy="15" r="7"/><ellipse cx="15" cy="15" rx="3" ry="7"/><path d="M8 15h14M9 11.5h12M9 18.5h12"/></g></svg>
        <span class="contact-icons__rule"></span>
      </div>
      <ul class="contact-list">
        <li>587-412-9065</li>
        <li>colinvardek@mailora.com</li>
        <li>colinvardek.ca</li>
      </ul>
    </div>
  </section>

  <section class="card card-back">
    <div class="card-back__pattern" aria-hidden="true">
      <p class="pattern-row" style="top:24px">The Harbourline Property Group &nbsp; The Harbourline Property Group</p>
      <p class="pattern-row" style="top:94px">The Harbourline Property Group &nbsp; The Harbourline Property Group</p>
      <p class="pattern-row" style="top:164px">The Harbourline Property Group &nbsp; The Harbourline Property Group</p>
      <p class="pattern-row" style="top:234px">The Harbourline Property Group &nbsp; The Harbourline Property Group</p>
      <p class="pattern-row" style="top:420px">The Harbourline Property Group &nbsp; The Harbourline Property Group</p>
      <p class="pattern-row" style="top:490px">The Harbourline Property Group &nbsp; The Harbourline Property Group</p>
      <p class="pattern-row" style="top:560px">The Harbourline Property Group &nbsp; The Harbourline Property Group</p>
      <p class="pattern-row" style="top:630px">The Harbourline Property Group &nbsp; The Harbourline Property Group</p>
    </div>
    <div class="card-back__brand">
      <span class="brand-mark" aria-hidden="true"></span>
      <p class="brand-name">The Harbourline<br>Property Group</p>
    </div>
  </section>
</body>
</html>
```